Unternehmen für Ordnung und Sauberkeit am Arbeitsplatz und Produkte zur Produktionsoptimierung benötigt Visitenkarten und Briefpapier
Zielgruppe
Produkte für Ordnung und Sauberkeit am Arbeitsplatz, Organisation von Arbeitsplätzen, Produkte zur Vereinfachung von Arbeitsabläufen, Produkte zur Produktionsoptimierung unter dem Lean Gedanke, Schlagwort: "5S", nachhaltig, sauber
Aufgabenstellung
Wir sind auf der Suche nach Visitenkarten und Briefpapier für das Unternehmen yourTidor. Nachhaltig, Sauber usw.. Unser Firmenlogo finden Sie anbei.

```html
<!DOCTYPE html>
<html lang="de">
<head>
<meta charset="utf-8">
<title>yourTidor – Visitenkarte</title>
<link rel="stylesheet" href="https://fonts.googleapis.com/css2?family=PT+Sans:wght@400;700&display=swap">
<style>
  :root {
    --backdrop: #a8a8a8;
    --card-white: #ffffff;
    --brand-green: #1f8442;
    --ink: #1b1b1b;
    --ink-soft: #2a2a2a;
    --logo-grey: #3d3d3d;
    --font: "PT Sans", sans-serif;
  }
  html, body {
    margin: 0;
    padding: 0;
    width: 1163px;
    height: 1200px;
    overflow: hidden;
    background: var(--backdrop);
    font-family: var(--font);
  }
  .stage { position: relative; width: 1163px; height: 1200px; }

  .card { position: absolute; width: 736px; height: 421px; }

  /* Front */
  .card--front { left: 156px; top: 189px; background: var(--card-white); }
  .brand { position: absolute; display: flex; align-items: center; gap: 12px; }
  .brand__mark { display: block; }
  .brand__name { font-weight: 700; line-height: 1; }
  .card--front .brand { left: 470px; top: 78px; }
  .card--front .brand__mark { width: 44px; height: 44px; background: var(--brand-green); }
  .card--front .brand__name { font-size: 44px; color: var(--logo-grey); }

  .person__name {
    position: absolute; left: 44px; top: 214px; margin: 0;
    font-size: 20px; font-weight: 700; color: var(--ink);
  }
  .person__role {
    position: absolute; left: 46px; top: 249px; margin: 0;
    font-size: 15px; color: var(--ink-soft);
  }
  .rule {
    position: absolute; left: 264px; top: 228px; right: 0; height: 3px;
    background: var(--brand-green);
  }
  .contact {
    position: absolute; margin: 0; font-style: normal;
    font-size: 16px; line-height: 23px; color: var(--ink-soft);
  }
  .contact--address { left: 46px; top: 318px; }
  .contact--web { left: 268px; top: 341px; }
  .contact--phone { left: 502px; top: 341px; }
  .band {
    position: absolute; left: 0; right: 0; bottom: 0; height: 13px;
    background: var(--brand-green);
  }

  /* Back */
  .card--back {
    left: 293px; top: 681px; width: 721px; height: 416px;
    background: var(--brand-green);
    display: flex; align-items: center; justify-content: center;
  }
  .card--back .brand { position: static; gap: 16px; }
  .card--back .brand__mark { width: 60px; height: 60px; background: var(--card-white); }
  .card--back .brand__name { font-size: 64px; color: var(--card-white); }
</style>
</head>
<body>
<main class="stage">
  <section class="card card--front" aria-label="Visitenkarte Vorderseite">
    <div class="brand">
      <span class="brand__mark"></span>
      <span class="brand__name">yourTidor</span>
    </div>
    <h1 class="person__name">Jonas Weidlich</h1>
    <p class="person__role">Geschäftsführer</p>
    <div class="rule"></div>
    <address class="contact contact--address">Lindenweg 27<br>79341 Kenzfeld<br>Germany</address>
    <p class="contact contact--web">mail: kontakt@tidorwerk.de<br>www.tidorwerk.de</p>
    <p class="contact contact--phone">tel: 0 31 44 / 72 81 60<br>fax: 0 31 44 / 72 81 699</p>
    <div class="band"></div>
  </section>

  <section class="card card--back" aria-label="Visitenkarte Rückseite">
    <div class="brand">
      <span class="brand__mark"></span>
      <span class="brand__name">yourTidor</span>
    </div>
  </section>
</main>
</body>
</html>
```